Communication and Marketing agency needs a new presentation card

We are a group of communication and marketing agencies specialized in companies that are in the logistics and industrial sector. The head agency is TELVANO Grupo and the group consists of 4 agencies: TELVANO Media, TELVANO Digital, TELVANO Research and DifundeEnPantalla. We hace 4 offices in Spain (Madrid, Barcelona, Valencia and Murcia). We are looking for a clean and attractive design that transmits our experience, brand presence in the market and knowledge to those who receive the card.It has to maintain the colors of the logo that is attached.
Target Market(s)
logistics and industrial sector
Marketing department
Contact Information for Business Card
Clean and attractive design

```html
<!DOCTYPE html>
<html lang="es">
<head>
<meta charset="utf-8">
<title>TELVANO Grupo — Tarjeta de presentación</title>
<link rel="stylesheet" href="https://fonts.googleapis.com/css2?family=Josefin+Sans:wght@400&family=Oswald:wght@500&display=swap">
<style>
  :root {
    --charcoal: #2e2926;
    --brand-red: #b01f2a;
    --headline-grey: #8c8c8e;
    --paper-light: #f6f6f7;
    --paper-shade: #dcdde0;
    --white: #ffffff;
  }
  html, body {
    margin: 0;
    padding: 0;
    width: 1200px;
    height: 686px;
    overflow: hidden;
    background: var(--charcoal);
  }
  .card {
    position: relative;
    width: 1200px;
    height: 686px;
    overflow: hidden;
    background: var(--charcoal);
  }
  .card-shapes {
    position: absolute;
    inset: 0;
  }
  .group-name {
    position: absolute;
    left: 69px;
    top: 268px;
    margin: 0;
    font-family: "Josefin Sans", sans-serif;
    font-weight: 400;
    font-size: 68px;
    line-height: 80px;
    letter-spacing: 0;
    text-transform: uppercase;
    white-space: nowrap;
    color: var(--brand-red);
  }
  .group-name-line {
    display: block;
  }
  .group-name-soft {
    color: var(--headline-grey);
  }
  .agency {
    position: absolute;
    margin: 0;
    text-align: right;
    font-family: "Oswald", sans-serif;
    font-weight: 500;
    color: var(--white);
    line-height: 1;
  }
  .agency-name {
    display: block;
    font-size: 31px;
    letter-spacing: 1px;
  }
  .agency-unit {
    display: block;
    font-size: 17px;
    margin-top: 2px;
  }
  .agency--digital  { right: 178px; top: 372px; }
  .agency--media    { right: 220px; top: 449px; }
  .agency--grupo    { right: 251px; top: 518px; }
  .agency--research { right: 285px; top: 587px; }
</style>
</head>
<body>
<div class="card">
  <svg class="card-shapes" width="1200" height="686" viewBox="0 0 1200 686" aria-hidden="true">
    <defs>
      <radialGradient id="paper-glow" cx="1110" cy="340" r="330" gradientUnits="userSpaceOnUse">
        <stop offset="0" stop-color="#f6f6f7"/>
        <stop offset="1" stop-color="#dcdde0"/>
      </radialGradient>
    </defs>
    <polygon class="paper-panel" points="1100,0 1200,0 1200,686 900,686" fill="url(#paper-glow)"/>
    <polygon class="red-band" points="746,0 1200,0 1200,64 930,686 452,686" fill="#b01f2a"/>
    <g class="divider-lines" stroke="#ffffff" stroke-width="1.2">
      <line x1="561" y1="435" x2="1040" y2="435"/>
      <line x1="527" y1="509" x2="1009" y2="509"/>
      <line x1="500" y1="578" x2="979" y2="578"/>
    </g>
  </svg>

  <h1 class="group-name">
    <span class="group-name-line">Difunde</span>
    <span class="group-name-line"><span class="group-name-soft">En</span>Pantalla</span>
  </h1>

  <p class="agency agency--digital"><span class="agency-name">TELVANO</span><span class="agency-unit">Digital</span></p>
  <p class="agency agency--media"><span class="agency-name">TELVANO</span><span class="agency-unit">Media</span></p>
  <p class="agency agency--grupo"><span class="agency-name">TELVANO</span><span class="agency-unit">Grupo</span></p>
  <p class="agency agency--research"><span class="agency-name">TELVANO</span><span class="agency-unit">Research</span></p>
</div>
</body>
</html>
```